BUSINESS CARD DESIGN

NAME- DALE VORSKIN
PHONE NUMER - 555- 714-9082
EMAIL- OFFICE@TRV-GROUNDMAKRZ.COM
BACK OF CARD- SPEACIALIZES IN LAND CLEARING, FORESTRY MUCLHING AND EXCAVATION

Contact Information for Business Card

NAME- DALE VORSKIN PHONE NUMER - 555- 714-9082 EMAIL- OFFICE@TRV-GROUNDMAKRZ.COM BACK OF CARD- SPEACIALIZES IN LAND CLEARING , MUCLHING AND EXCAVATION

```html
<!DOCTYPE html>
<html lang="en">
<head>
<meta charset="utf-8">
<title>Trevane Ground Makrz LLC — Business Card</title>
<link rel="stylesheet" href="https://fonts.googleapis.com/css2?family=Audiowide&family=Roboto:wght@400;500&display=swap">
<style>
  :root {
    --stage: #18181a;
    --card-top: #2e2e30;
    --card-bottom: #232325;
    --gold: #fdb913;
    --gold-deep: #f7941d;
    --ink-light: #f2f2f2;
    --ink-dark: #2a2a2b;
    --ghost: rgba(255, 255, 255, 0.035);
  }
  * { box-sizing: border-box; margin: 0; padding: 0; }
  html, body {
    width: 1200px; height: 840px; overflow: hidden;
    background: var(--stage);
  }
  .stage { position: relative; width: 1200px; height: 840px; }

  .card {
    position: absolute;
    width: 560px; height: 320px;
    border-radius: 20px;
    background: linear-gradient(160deg, var(--card-top), var(--card-bottom));
    border-bottom: 4px solid var(--gold);
    border-left: 2px solid var(--gold);
    box-shadow: 0 18px 40px rgba(0, 0, 0, 0.55);
    overflow: hidden;
  }
  .card--back { left: 60px; top: 70px; }
  .card--front { left: 580px; top: 440px; }

  /* brand lockup */
  .brand { display: flex; flex-direction: column; align-items: center; }
  .brand__mark {
    width: 26px; height: 26px; border-radius: 50%;
    background: var(--gold); margin-bottom: 10px;
  }
  .brand__name {
    font-family: "Audiowide", sans-serif;
    color: var(--gold);
    font-size: 22px; letter-spacing: 1px; line-height: 1.15;
    text-align: center;
  }
  .brand__sub {
    font-family: "Audiowide", sans-serif;
    color: var(--gold);
    font-size: 12px; letter-spacing: 7px; margin-top: 4px;
  }
  .brand__rules { width: 300px; margin-top: 8px; }
  .brand__rules span { display: block; height: 2px; background: var(--gold); margin: 5px 0; }
  .brand__rules span:nth-child(1) { width: 80%; margin-left: 20%; }
  .brand__rules span:nth-child(2) { width: 60%; margin-left: 6%; }

  /* back side */
  .card--back .brand { margin-top: 40px; }
  .specialty {
    margin: 18px auto 0; width: max-content;
    background: var(--gold); color: var(--ink-dark);
    font-family: "Audiowide", sans-serif;
    font-size: 20px; padding: 4px 16px; letter-spacing: 1px;
  }
  .services {
    margin-top: 18px; text-align: center;
    font-family: "Roboto", sans-serif; font-size: 16px;
    color: var(--ink-light); letter-spacing: 0.5px;
  }
  .services .dot { color: var(--gold); margin: 0 6px; }

  /* front side */
  .ghost-mark {
    position: absolute; left: 60px; top: 40px;
    width: 260px; height: 260px; border-radius: 50%;
    background: var(--ghost);
  }
  .card--front .brand { position: absolute; right: 30px; top: 26px; }
  .card--front .brand__rules { width: 240px; }
  .divider-top {
    position: absolute; left: 250px; right: 24px; top: 176px;
    height: 1px; background: var(--ink-light);
  }
  .person {
    position: absolute; left: 34px; top: 196px;
    font-family: "Audiowide", sans-serif; font-size: 28px;
    color: var(--gold); letter-spacing: 1px;
  }
  .divider-bottom {
    position: absolute; left: 34px; width: 300px; top: 242px;
    height: 1px; background: var(--ink-light);
  }
  .contact {
    position: absolute; left: 34px; top: 256px;
    display: flex; gap: 22px; align-items: center;
    font-family: "Roboto", sans-serif; font-size: 17px; color: var(--ink-light);
  }
  .contact__item { display: flex; align-items: center; gap: 8px; }
  .contact__item svg { width: 18px; height: 18px; fill: var(--gold); }
</style>
</head>
<body>
<main class="stage">

  <section class="card card--back" aria-label="Back of card">
    <div class="brand">
      <div class="brand__mark"></div>
      <div class="brand__name">TREVANE GROUND MAKRZ LLC</div>
      <div class="brand__sub">HAWAII</div>
      <div class="brand__rules"><span></span><span></span></div>
    </div>
    <div class="specialty">SPEACIALIZES IN</div>
    <p class="services"><span class="dot">●</span>LAND CLEARING <span class="dot">●</span> MUCLHING <span class="dot">●</span> EXCAVATION</p>
  </section>

  <section class="card card--front" aria-label="Front of card">
    <div class="ghost-mark"></div>
    <div class="brand">
      <div class="brand__mark"></div>
      <div class="brand__name">TREVANE GROUND<br>MAKRZ LLC</div>
      <div class="brand__sub">HAWAII</div>
      <div class="brand__rules"><span></span><span></span></div>
    </div>
    <div class="divider-top"></div>
    <h1 class="person">DALE VORSKIN</h1>
    <div class="divider-bottom"></div>
    <div class="contact">
      <span class="contact__item">
        <svg viewBox="0 0 24 24" aria-hidden="true"><path d="M6.6 10.8a15.1 15.1 0 0 0 6.6 6.6l2.2-2.2a1 1 0 0 1 1-.25 11.4 11.4 0 0 0 3.6.57 1 1 0 0 1 1 1V20a1 1 0 0 1-1 1A17 17 0 0 1 3 4a1 1 0 0 1 1-1h3.5a1 1 0 0 1 1 1c0 1.25.2 2.45.57 3.57a1 1 0 0 1-.25 1z"/></svg>
        555- 714-9082
      </span>
      <span class="contact__item">
        <svg viewBox="0 0 24 24" aria-hidden="true"><path d="M3 5h18a1 1 0 0 1 1 1v12a1 1 0 0 1-1 1H3a1 1 0 0 1-1-1V6a1 1 0 0 1 1-1zm9 7.5L20 7H4z"/></svg>
        office@trv-groundmakrz.com
      </span>
    </div>
  </section>

</main>
</body>
</html>
```